New Interrior Decoration company needs new website

We need a website for our new company specialising in interior decoration to residential and commercial markets.
We supply and install decorative and printed films for office and home decoration such as feature walls.
We would like to keep the design simple and clean.

Target Market(s)

Architects and interior designaers

Industry/Entity Type

It Company

Number of Pages Required

5+ page

Font styles to use
Sans Serif

Requirements
Must have
• Home page,
• Services/products page (split into commercial and residential)
• Gallery (split into commercial and residential)
• contact form and page
Nice to have
• Very clean and minimalistic design.

```html
<!DOCTYPE html>
<html lang="en">
<head>
<meta charset="utf-8">
<title>Norvale Interiors</title>
<link href="https://fonts.googleapis.com/css2?family=Raleway:wght@400;500;600&family=Open+Sans:wght@400;600;700&display=swap" rel="stylesheet">
<style>
:root{
  --blue:#0b5cb5;
  --ink:#2f2f2f;
  --text:#555555;
  --grey-bg:#eeeeee;
  --white:#ffffff;
  --dark:#3a3a3a;
  --darker:#2b2b2b;
  --field:#f4f4f4;
  --field-line:#cfcfcf;
}
*{margin:0;padding:0;box-sizing:border-box}
html,body{width:1200px;height:2740px;overflow:hidden;background:var(--white)}
body{position:relative;font-family:"Open Sans",sans-serif;color:var(--text)}
.abs{position:absolute}
.heading{font-family:"Raleway",sans-serif;font-weight:400;color:var(--ink);text-transform:uppercase}
.heading span{color:var(--blue)}
.btn{position:absolute;background:var(--blue);color:var(--white);font-family:"Raleway",sans-serif;font-size:20px;display:flex;align-items:center;justify-content:center;text-transform:uppercase;border-radius:3px}

/* header */
.site-header{left:0;top:0;width:1200px;height:105px;background:var(--white)}
.brand{left:77px;top:24px;display:flex;align-items:center;gap:14px}
.brand-square{width:52px;height:52px;background:var(--blue)}
.brand-name{font-family:"Raleway",sans-serif;font-weight:600;font-size:34px;line-height:1;color:var(--ink);text-transform:uppercase;width:220px}
.main-nav{left:488px;top:29px;height:51px;display:flex;font-family:"Raleway",sans-serif;font-size:21px;color:var(--ink)}
.main-nav a{display:flex;align-items:center;padding:0 25px;text-decoration:none;color:inherit}
.main-nav a.active{background:var(--blue);color:var(--white);padding:0 26px}

.hero{left:0;top:105px;width:1200px;height:575px;background:linear-gradient(180deg,#8b8c8a 0%,#cfd3d4 45%,#6b6a67 100%)}

/* call band */
.call-band{left:0;top:680px;width:1200px;height:142px;background:var(--dark)}
.call-band svg{position:absolute;left:0;top:0}
.call-label{left:77px;top:726px;font-family:"Raleway",sans-serif;font-size:27px;color:var(--white)}
.call-icon{left:277px;top:713px}
.call-number{left:352px;top:722px;font-size:31px;font-weight:700;color:var(--white)}
.call-text{left:660px;top:700px;width:440px;font-size:15.5px;line-height:26px;color:#e6e6e6}
.call-mail{left:658px;top:763px;display:flex;align-items:center;gap:12px;font-size:16px;color:#e6e6e6}

/* services */
.services{left:0;top:822px;width:1200px;height:320px;background:var(--grey-bg)}
.services-title{left:0;top:860px;width:1200px;text-align:center;font-size:47px}
.service-img{width:208px;height:140px;top:940px}
.service-name{top:934px;font-family:"Raleway",sans-serif;font-size:26px;color:var(--ink)}
.service-text{top:970px;width:270px;font-size:15.5px;line-height:25px}
.service-more{top:1058px;font-family:"Raleway",sans-serif;font-size:18px;color:var(--blue)}

/* welcome */
.welcome-kicker{left:77px;top:1190px;font-size:31px}
.welcome-title{left:77px;top:1232px;font-family:"Raleway",sans-serif;font-size:45px;color:var(--blue);text-transform:uppercase}
.welcome-text{left:77px;top:1292px;width:610px;font-size:15.5px;line-height:25px}
.welcome-mark{left:737px;top:1200px;width:385px;height:246px;display:flex;align-items:center;justify-content:center;gap:22px}
.welcome-mark .sq{width:90px;height:90px;background:var(--blue)}
.welcome-mark .nm{font-family:"Raleway",sans-serif;font-weight:600;font-size:40px;line-height:1.05;color:var(--ink);text-transform:uppercase}

/* gallery */
.gallery{left:0;top:1518px;width:1200px;height:438px;background:var(--grey-bg)}
.gallery-title{left:0;top:1570px;width:1200px;text-align:center;font-size:47px}
.gallery-img{top:1643px;width:234px;height:157px}

/* testimonial + contact */
.section-title{top:1992px;font-size:34px}
.quote{left:77px;top:2046px;width:490px;font-size:15.5px;line-height:25px}
.avatar{left:77px;top:2155px;width:104px;height:104px;border-radius:50%;background:radial-gradient(circle at 50% 40%,#d8d8d8,#a9a9a9)}
.client-name{left:196px;top:2196px;font-size:16px;font-weight:700;color:var(--blue)}
.arrow-btn{top:2290px;width:47px;height:47px;background:var(--blue);border-radius:3px;display:flex;align-items:center;justify-content:center}
.field{position:absolute;background:var(--field);border:1px solid var(--field-line);font-size:15px;color:#666;padding:10px 11px}

/* footer */
.site-footer{left:0;top:2402px;width:1200px;height:286px;background:var(--dark);color:#e8e8e8}
.foot-brand{left:77px;top:2438px;display:flex;align-items:center;gap:10px}
.foot-brand .sq{width:34px;height:34px;background:var(--blue)}
.foot-brand .nm{font-family:"Raleway",sans-serif;font-weight:600;font-size:21px;line-height:1;color:var(--white);text-transform:uppercase;width:160px}
.foot-about{left:77px;top:2496px;width:240px;font-size:15.5px;line-height:26px;color:#e8e8e8}
.foot-title{top:2428px;font-family:"Raleway",sans-serif;font-size:24px;color:var(--white)}
.foot-links{left:348px;top:2472px;list-style:none;font-size:17.5px;line-height:36.5px;color:#e8e8e8}
.foot-links li::before{content:"\2192";margin-right:10px}
.foot-contact{left:620px;font-size:15.5px;color:#e8e8e8;display:flex;gap:10px}
.social{top:2604px;width:46px;height:46px;border:1.5px solid #cfcfcf;background:var(--white)}
.foot-field{position:absolute;left:888px;width:234px;height:36px;background:#545454;color:#f0f0f0;font-size:15px;padding:8px 10px}
.copyright{left:0;top:2688px;width:1200px;height:52px;background:var(--darker);color:#e8e8e8;font-size:15.5px;display:flex;align-items:center;justify-content:center}
</style>
</head>
<body>

<header class="abs site-header">
  <div class="abs brand"><div class="brand-square"></div><div class="brand-name">Norvale Interiors</div></div>
  <nav class="abs main-nav">
    <a class="active">HOME</a><a>ABOUT</a><a>SERVICES</a><a>GALLERY</a><a>CONTACT</a>
  </nav>
</header>

<div class="abs hero" role="img" aria-label="Photo of a modern open-plan kitchen and dining room with pendant lamps"></div>

<section class="abs call-band">
  <svg width="630" height="142" viewBox="0 0 630 142"><polygon points="0,0 582,0 625,71 582,142 0,142" fill="#0b5cb5"/><polygon points="582,0 594,0 637,71 594,142 582,142 625,71" fill="#ffffff"/></svg>
</section>
<div class="abs call-label">CALL US NOW!</div>
<svg class="abs call-icon" width="66" height="66" viewBox="0 0 66 66"><circle cx="33" cy="33" r="31" fill="none" stroke="#fff" stroke-width="2"/><path d="M24 20c2-1 4 0 5 2l2 5c0 2-1 3-2 4 1 3 4 6 7 7 1-1 2-2 4-2l5 2c2 1 3 3 2 5-1 3-4 4-7 3-8-2-15-9-17-17-1-3 0-7 1-9z" fill="#fff"/></svg>
<div class="abs call-number">123 456 7890</div>
<p class="abs call-text">Lorem Ipsum is simply dummy text of the printing and typesetting industry lorem Ipsum has been.</p>
<div class="abs call-mail"><svg width="20" height="15" viewBox="0 0 20 15"><rect x="1" y="1" width="18" height="13" fill="none" stroke="#e6e6e6" stroke-width="1.6"/><path d="M1 1l9 7 9-7" fill="none" stroke="#e6e6e6" stroke-width="1.6"/></svg>info@norvaleinteriors.com</div>

<section class="abs services"></section>
<h2 class="abs heading services-title">Services <span>We Provide</span></h2>
<div class="abs service-img" style="left:77px;background:linear-gradient(135deg,#6f7a7c,#c9cfcf 60%,#55605f)" role="img" aria-label="Residential interior with decorative wall film"></div>
<h3 class="abs service-name" style="left:303px">Residential Interiors</h3>
<p class="abs service-text" style="left:303px">Lorem Ipsum is simply dummy text of the printing and typesetting industry Lorem Ipsum...</p>
<div class="abs service-more" style="left:303px">READ MORE &#187;</div>
<div class="abs service-img" style="left:628px;background:linear-gradient(135deg,#d8d0c8,#efe8e2 55%,#b5584e)" role="img" aria-label="Commercial office corridor with printed glass film"></div>
<h3 class="abs service-name" style="left:855px">Commercial Interiors</h3>
<p class="abs service-text" style="left:855px">Lorem Ipsum is simply dummy text of the printing and typesetting industry Lorem Ipsum...</p>
<div class="abs service-more" style="left:855px">READ MORE &#187;</div>

<h2 class="abs heading welcome-kicker">Welcome to</h2>
<h1 class="abs welcome-title">Norvale Interiors</h1>
<p class="abs welcome-text">Lorem Ipsum is simply dummy text of the printing and typesetting industry. Lorem Ipsum has been the industry's standard dummy text ever since the 1500s, when an unknown printer took a galley of type and scrambled it to make a type specimen book.</p>
<div class="btn" style="left:77px;top:1408px;width:166px;height:50px">Read More</div>
<div class="abs welcome-mark"><div class="sq"></div><div class="nm">Norvale<br>Interiors</div></div>

<section class="abs gallery"></section>
<h2 class="abs heading gallery-title">Latest <span>Gallery</span></h2>
<div class="abs gallery-img" style="left:77px;background:linear-gradient(135deg,#2a2522,#6d5c4e)" role="img" aria-label="Dark lounge with black vases"></div>
<div class="abs gallery-img" style="left:348px;background:linear-gradient(135deg,#3a1a12,#8a3a22 60%,#c9b8c4)" role="img" aria-label="Lounge chair against a red textured wall"></div>
<div class="abs gallery-img" style="left:619px;background:linear-gradient(135deg,#6b6d66,#a9aba4)" role="img" aria-label="Stone-effect feature wall in a hallway"></div>
<div class="abs gallery-img" style="left:888px;background:linear-gradient(90deg,#9a3b2a,#c25a3e 55%,#d8d8d4)" role="img" aria-label="Brick-effect wall with black sofa"></div>
<div class="btn" style="left:525px;top:1834px;width:150px;height:51px;font-size:19px">View All</div>

<h2 class="abs heading section-title" style="left:77px">What our <span>Client say</span></h2>
<p class="abs quote">Lorem Ipsum is simply dummy text of the printing and typesetting industry. Lorem Ipsum has been the industry's standard dummy text ever since the 1500s, when an unknown printer took a galley of type and scrambled it to make a type specimen book.</p>
<div class="abs avatar" role="img" aria-label="Client portrait"></div>
<div class="abs client-name">- CLIENT NAME</div>
<div class="abs arrow-btn" style="left:77px"><svg width="14" height="24" viewBox="0 0 14 24"><path d="M12 2L3 12l9 10" fill="none" stroke="#fff" stroke-width="2"/></svg></div>
<div class="abs arrow-btn" style="left:140px"><svg width="14" height="24" viewBox="0 0 14 24"><path d="M2 2l9 10-9 10" fill="none" stroke="#fff" stroke-width="2"/></svg></div>

<h2 class="abs heading section-title" style="left:637px">Get in <span>Touch with us</span></h2>
<div class="field" style="left:645px;top:2045px;width:228px;height:42px">Enter Name</div>
<div class="field" style="left:894px;top:2045px;width:228px;height:42px">Enter Contact No.</div>
<div class="field" style="left:645px;top:2108px;width:477px;height:42px">Enter Email Id</div>
<div class="field" style="left:645px;top:2170px;width:477px;height:95px">Enter Message</div>
<div class="btn" style="left:645px;top:2285px;width:142px;height:52px;font-size:21px;border-radius:0">Submit</div>

<footer class="abs site-footer"></footer>
<div class="abs foot-brand"><div class="sq"></div><div class="nm">Norvale Interiors</div></div>
<p class="abs foot-about">Lorem Ipsum is simply dummy text of the printing and typesetting industry. Lorem Ipsum has been the industry's standard dummy text ever since the 1500.</p>
<h4 class="abs foot-title" style="left:350px">Useful Links</h4>
<ul class="abs foot-links"><li>Home</li><li>About</li><li>Services</li><li>Gallery</li><li>Contact</li></ul>
<h4 class="abs foot-title" style="left:620px">Get In Touch</h4>
<div class="abs foot-contact" style="top:2470px;width:240px;line-height:24px"><svg width="14" height="20" viewBox="0 0 14 20" style="flex:none;margin-top:3px"><path d="M7 0C3 0 0 3 0 7c0 5 7 13 7 13s7-8 7-13c0-4-3-7-7-7zm0 10a3 3 0 110-6 3 3 0 010 6z" fill="#fff"/></svg>Lorem Ipsum is dummy text of the printing.</div>
<div class="abs foot-contact" style="top:2526px;font-weight:700;color:#fff"><svg width="18" height="18" viewBox="0 0 24 24"><path d="M5 2c2-1 3 0 4 2l1 4c0 2-1 2-2 3 1 3 4 6 7 7 1-1 1-2 3-2l4 1c2 1 3 2 2 4-1 3-4 4-7 3C10 22 3 15 1 8 0 5 2 3 5 2z" fill="#fff"/></svg>123 456 7890</div>
<div class="abs foot-contact" style="top:2566px"><svg width="20" height="15" viewBox="0 0 20 15" style="margin-top:3px"><rect x="1" y="1" width="18" height="13" fill="none" stroke="#e8e8e8" stroke-width="1.6"/><path d="M1 1l9 7 9-7" fill="none" stroke="#e8e8e8" stroke-width="1.6"/></svg>info@norvaleinteriors.com</div>
<div class="abs social" style="left:620px"></div>
<div class="abs social" style="left:690px"></div>
<div class="abs social" style="left:760px"></div>
<h4 class="abs foot-title" style="left:890px">Newsletter</h4>
<div class="foot-field" style="top:2476px">Enter Name</div>
<div class="foot-field" style="top:2528px">Enter Email</div>
<div class="btn" style="left:888px;top:2580px;width:152px;height:48px;font-size:19px;border-radius:0">Subscribe</div>
<div class="abs copyright">©&nbsp;<b>NORVALE INTERIORS</b>&nbsp;- 2016. All Rights Reserved.</div>

</body>
</html>
```